Small Cosmetics Business needs a label design

We need a label design to affix on our cosmetic products made in Norfolk, England. The label needs to have the manufacturer's name, the product name, an ingredients list, an indication of use (ritual), contact details of manufacturer, weight, period after opening logo, batch number. We would like the label to highlight (in the form of sticker or tags) that the products are 100% natural, that they are hand made, that they do not contain preservatives or chemicals.Attached is a file with typical information for the label. The label should have colours, clarity and evoke nature, luxury.

Target Market(s)

UK

Industry/Entity Type

Cosmetics

Logo Text

Tesori Buna, Shape Radiance

Font styles to use
Decorative

```html
<!DOCTYPE html>
<html lang="en">
<head>
<meta charset="utf-8">
<title>Tesori Buna — Hair Butter Labels</title>
<link rel="stylesheet" href="https://fonts.googleapis.com/css2?family=Rokkitt:wght@600&family=Mulish:wght@400;600&display=swap">
<style>
  :root {
    --paper: #ffffff;
    --panel: #c4c4c4;
    --ink: #1e1e1e;
    --muted: #555555;
    --velvet: #e5207f;
    --honey: #2e8b3a;
    --lotus: #1ba3e0;
    --natural: #3a9a3f;
    --flower-blue: #7cc8f2;
    --flower-yellow: #f6cf2a;
    --flower-pink: #ef6fa6;
    --flower-green: #5cbf3c;
  }
  * { box-sizing: border-box; margin: 0; padding: 0; }
  html, body { width: 1200px; height: 600px; overflow: hidden; }
  body {
    display: flex;
    font-family: "Mulish", sans-serif;
    color: var(--ink);
    background: var(--paper);
  }
  .range { width: 845px; height: 600px; display: flex; flex-direction: column; justify-content: center; gap: 48px; padding: 0 32px; }
  .row { display: flex; justify-content: space-between; align-items: center; }
  .showcase { width: 355px; height: 600px; background: var(--panel); display: flex; flex-direction: column; align-items: center; justify-content: center; gap: 70px; }

  .wrap-label {
    width: 250px; height: 128px; background: var(--paper);
    border: 1px solid #e2e2e2;
    display: grid; grid-template-columns: 26px 40px 1fr 40px 26px;
    align-items: center;
  }
  .side-text { font-size: 4.5px; line-height: 1.4; color: var(--muted); padding: 0 3px; }
  .floral { position: relative; height: 96px; }
  .floral-art { width: 100%; height: 100%; border-radius: 40%;
    background: radial-gradient(circle at 30% 30%, var(--flower-blue), transparent 60%),
                radial-gradient(circle at 70% 60%, var(--flower-yellow), transparent 60%),
                radial-gradient(circle at 40% 85%, var(--flower-green), transparent 55%),
                radial-gradient(circle at 75% 20%, var(--flower-pink), transparent 55%); }
  .centre { text-align: center; padding: 0 2px; }
  .brand { font-family: "Rokkitt", serif; font-weight: 600; font-size: 15px; color: var(--ink); display: inline-flex; align-items: center; gap: 3px; white-space: nowrap; }
  .brand::before { content: ""; width: 5px; height: 5px; border-radius: 50%; background: var(--ink); }
  .product { font-size: 13px; margin-top: 1px; white-space: nowrap; }
  .claim { font-size: 5px; line-height: 1.35; margin-top: 6px; }
  .volume { font-size: 5px; margin-top: 4px; }
  .badge { position: absolute; left: -6px; top: 28px; width: 24px; height: 24px; border: 1.5px solid var(--natural); border-radius: 50%; color: var(--natural); font-size: 4.5px; font-weight: 600; display: flex; align-items: center; justify-content: center; text-align: center; line-height: 1.1; background: var(--paper); }
  .velvet { color: var(--velvet); } .honey { color: var(--honey); } .lotus { color: var(--lotus); }

  .lid-label { width: 200px; height: 200px; display: block; }
  .lid-label.small { width: 170px; height: 170px; }
  .lid-ring-text { font-family: "Mulish", sans-serif; font-size: 14px; letter-spacing: 0.5px; }
  .lid-address { font-family: "Mulish", sans-serif; font-size: 9.5px; }
  .lid-brand { font-family: "Rokkitt", serif; font-weight: 600; font-size: 17px; }
  .lid-product { font-family: "Mulish", sans-serif; font-size: 13px; }
  .lid-volume { font-family: "Mulish", sans-serif; font-size: 7px; }
</style>
</head>
<body>
  <main class="range">
    <section class="row wrap-labels">
      <article class="wrap-label">
        <p class="side-text">Ingredients: pure butters and plant oils.</p>
        <div class="floral"><div class="floral-art" role="img" aria-label="Colourful flower illustration"></div></div>
        <div class="centre">
          <div class="brand">Tesori Buna</div>
          <div class="product velvet">Velvet Bloom</div>
          <p class="claim">Repairs damaged hair,<br>nourishes and moisturise all types of hairs</p>
          <p class="volume">3.4 fl Oz 100ml</p>
        </div>
        <div class="floral"><div class="floral-art" role="img" aria-label="Colourful flower illustration"></div><span class="badge">100%<br>NATURAL</span></div>
        <p class="side-text">Best before: see base</p>
      </article>
      <article class="wrap-label">
        <p class="side-text">Ingredients: pure butters and plant oils.</p>
        <div class="floral"><div class="floral-art" role="img" aria-label="Colourful flower illustration"></div></div>
        <div class="centre">
          <div class="brand">Tesori Buna</div>
          <div class="product honey">Honey Glow</div>
          <p class="claim">Repairs damaged hair,<br>nourishes and moisturise all types of hairs</p>
          <p class="volume">3.4 fl Oz 100ml</p>
        </div>
        <div class="floral"><div class="floral-art" role="img" aria-label="Colourful flower illustration"></div><span class="badge">100%<br>NATURAL</span></div>
        <p class="side-text">Best before: see base</p>
      </article>
      <article class="wrap-label">
        <p class="side-text">Ingredients: pure butters and plant oils.</p>
        <div class="floral"><div class="floral-art" role="img" aria-label="Colourful flower illustration"></div></div>
        <div class="centre">
          <div class="brand">Tesori Buna</div>
          <div class="product lotus">Lotus Luxe</div>
          <p class="claim">Repairs damaged hair,<br>nourishes and moisturise all types of hairs</p>
          <p class="volume">3.4 fl Oz 100ml</p>
        </div>
        <div class="floral"><div class="floral-art" role="img" aria-label="Colourful flower illustration"></div><span class="badge">100%<br>NATURAL</span></div>
        <p class="side-text">Best before: see base</p>
      </article>
    </section>

    <section class="row lid-labels">
      <svg class="lid-label small" viewBox="0 0 200 200" aria-label="Velvet Bloom lid label">
        <defs>
          <path id="topA" d="M 16,100 A 84,84 0 0,1 184,100"/>
          <path id="botA" d="M 14,100 A 86,86 0 0,0 186,100"/>
          <linearGradient id="flA" x1="0" x2="1"><stop offset="0" stop-color="#7cc8f2"/><stop offset=".35" stop-color="#ef6fa6"/><stop offset=".7" stop-color="#f6cf2a"/><stop offset="1" stop-color="#5cbf3c"/></linearGradient>
        </defs>
        <circle cx="100" cy="100" r="98" fill="#e5207f"/>
        <circle cx="100" cy="100" r="72" fill="#fff"/>
        <text class="lid-ring-text" fill="#fff"><textPath href="#topA" startOffset="50%" text-anchor="middle">HANDMADE IN NORFOLK</textPath></text>
        <text class="lid-address" fill="#fff"><textPath href="#botA" startOffset="50%" text-anchor="middle" dominant-baseline="hanging">Tesori Buna, P.O. Box 48 Dereham NR19 1AB UK</textPath></text>
        <text class="lid-brand" x="100" y="74" text-anchor="middle" fill="#1e1e1e">Tesori Buna</text>
        <text class="lid-product" x="100" y="100" text-anchor="middle" fill="#e5207f">Velvet Bloom</text>
        <rect x="58" y="110" width="84" height="26" rx="13" fill="url(#flA)" opacity=".8" role="img" aria-label="Colourful flower illustration"/>
        <text class="lid-volume" x="100" y="150" text-anchor="middle" fill="#1e1e1e">1 fl Oz 30 ml</text>
      </svg>
      <svg class="lid-label small" viewBox="0 0 200 200" aria-label="Honey Glow lid label">
        <defs>
          <path id="topB" d="M 16,100 A 84,84 0 0,1 184,100"/>
          <path id="botB" d="M 14,100 A 86,86 0 0,0 186,100"/>
          <linearGradient id="flB" x1="0" x2="1"><stop offset="0" stop-color="#7cc8f2"/><stop offset=".35" stop-color="#ef6fa6"/><stop offset=".7" stop-color="#f6cf2a"/><stop offset="1" stop-color="#5cbf3c"/></linearGradient>
        </defs>
        <circle cx="100" cy="100" r="98" fill="#2e8b3a"/>
        <circle cx="100" cy="100" r="72" fill="#fff"/>
        <text class="lid-ring-text" fill="#fff"><textPath href="#topB" startOffset="50%" text-anchor="middle">HANDMADE IN NORFOLK</textPath></text>
        <text class="lid-address" fill="#fff"><textPath href="#botB" startOffset="50%" text-anchor="middle" dominant-baseline="hanging">Tesori Buna, P.O. Box 48 Dereham NR19 1AB UK</textPath></text>
        <text class="lid-brand" x="100" y="74" text-anchor="middle" fill="#1e1e1e">Tesori Buna</text>
        <text class="lid-product" x="100" y="100" text-anchor="middle" fill="#2e8b3a">Honey Glow</text>
        <rect x="58" y="110" width="84" height="26" rx="13" fill="url(#flB)" opacity=".8" role="img" aria-label="Colourful flower illustration"/>
        <text class="lid-volume" x="100" y="150" text-anchor="middle" fill="#1e1e1e">1 fl Oz 30 ml</text>
      </svg>
      <svg class="lid-label small" viewBox="0 0 200 200" aria-label="Lotus Luxe lid label">
        <defs>
          <path id="topC" d="M 16,100 A 84,84 0 0,1 184,100"/>
          <path id="botC" d="M 14,100 A 86,86 0 0,0 186,100"/>
          <linearGradient id="flC" x1="0" x2="1"><stop offset="0" stop-color="#7cc8f2"/><stop offset=".35" stop-color="#ef6fa6"/><stop offset=".7" stop-color="#f6cf2a"/><stop offset="1" stop-color="#5cbf3c"/></linearGradient>
        </defs>
        <circle cx="100" cy="100" r="98" fill="#1ba3e0"/>
        <circle cx="100" cy="100" r="72" fill="#fff"/>
        <text class="lid-ring-text" fill="#fff"><textPath href="#topC" startOffset="50%" text-anchor="middle">HANDMADE IN NORFOLK</textPath></text>
        <text class="lid-address" fill="#fff"><textPath href="#botC" startOffset="50%" text-anchor="middle" dominant-baseline="hanging">Tesori Buna, P.O. Box 48 Dereham NR19 1AB UK</textPath></text>
        <text class="lid-brand" x="100" y="74" text-anchor="middle" fill="#1e1e1e">Tesori Buna</text>
        <text class="lid-product" x="100" y="100" text-anchor="middle" fill="#1ba3e0">Lotus Luxe</text>
        <rect x="58" y="110" width="84" height="26" rx="13" fill="url(#flC)" opacity=".8" role="img" aria-label="Colourful flower illustration"/>
        <text class="lid-volume" x="100" y="150" text-anchor="middle" fill="#1e1e1e">1 fl Oz 30 ml</text>
      </svg>
    </section>
  </main>

  <aside class="showcase">
    <svg class="lid-label" viewBox="0 0 200 200" aria-label="Lotus Luxe lid label, blue ring">
      <defs>
        <path id="topD" d="M 16,100 A 84,84 0 0,1 184,100"/>
        <path id="botD" d="M 14,100 A 86,86 0 0,0 186,100"/>
        <linearGradient id="flD" x1="0" x2="1"><stop offset="0" stop-color="#7cc8f2"/><stop offset=".35" stop-color="#ef6fa6"/><stop offset=".7" stop-color="#f6cf2a"/><stop offset="1" stop-color="#5cbf3c"/></linearGradient>
      </defs>
      <circle cx="100" cy="100" r="98" fill="#1ba3e0"/>
      <circle cx="100" cy="100" r="72" fill="#fff"/>
      <text class="lid-ring-text" fill="#fff"><textPath href="#topD" startOffset="50%" text-anchor="middle">HANDMADE IN NORFOLK</textPath></text>
      <text class="lid-address" fill="#fff"><textPath href="#botD" startOffset="50%" text-anchor="middle" dominant-baseline="hanging">Tesori Buna, P.O. Box 48 Dereham NR19 1AB UK</textPath></text>
      <text class="lid-brand" x="100" y="74" text-anchor="middle" fill="#1e1e1e">Tesori Buna</text>
      <text class="lid-product" x="100" y="100" text-anchor="middle" fill="#1ba3e0">Lotus Luxe</text>
      <rect x="58" y="110" width="84" height="26" rx="13" fill="url(#flD)" opacity=".8" role="img" aria-label="Colourful flower illustration"/>
      <text class="lid-volume" x="100" y="150" text-anchor="middle" fill="#1e1e1e">1 fl Oz 30 ml</text>
    </svg>

    <svg class="lid-label" viewBox="0 0 200 200" aria-label="Velvet Bloom lid label, white ring">
      <defs>
        <path id="topE" d="M 16,100 A 84,84 0 0,1 184,100"/>
        <path id="botE" d="M 14,100 A 86,86 0 0,0 186,100"/>
        <linearGradient id="flE" x1="0" x2="1"><stop offset="0" stop-color="#7cc8f2"/><stop offset=".35" stop-color="#ef6fa6"/><stop offset=".7" stop-color="#f6cf2a"/><stop offset="1" stop-color="#5cbf3c"/></linearGradient>
      </defs>
      <circle cx="100" cy="100" r="98" fill="#fff" stroke="#1e1e1e" stroke-width="1.5"/>
      <circle cx="100" cy="100" r="72" fill="#fff" stroke="#1e1e1e" stroke-width="1"/>
      <circle cx="12" cy="100" r="2.5" fill="#1e1e1e"/>
      <circle cx="188" cy="100" r="2.5" fill="#1e1e1e"/>
      <text class="lid-ring-text" fill="#1e1e1e"><textPath href="#topE" startOffset="50%" text-anchor="middle">HANDMADE IN NORFOLK</textPath></text>
      <text class="lid-address" fill="#1e1e1e"><textPath href="#botE" startOffset="50%" text-anchor="middle" dominant-baseline="hanging">Tesori Buna, P.O. Box 48 Dereham NR19 1AB UK</textPath></text>
      <text class="lid-brand" x="100" y="74" text-anchor="middle" fill="#1e1e1e">Tesori Buna</text>
      <text class="lid-product" x="100" y="100" text-anchor="middle" fill="#e5207f">Velvet Bloom</text>
      <rect x="58" y="110" width="84" height="26" rx="13" fill="url(#flE)" opacity=".8" role="img" aria-label="Colourful flower illustration"/>
      <text class="lid-volume" x="100" y="150" text-anchor="middle" fill="#1e1e1e">1 fl Oz 30 ml</text>
    </svg>
  </aside>
</body>
</html>
```